Pawn & Gun store business card design

Hello! We would like a new business card design for our pawn & gun store. We loan money on items of value and sell firearms, jewelry, electronics & more.

Card will need to have the following information:

Business name - Prairie Nickel Pawn & Gun
Address - 2417 Hwy 53 S. Suite C Wylie, TX 75246
Employees name - Darren Kellum
Phone number - 972-613-8840
Email - PrairieNickelPawn@Mailvera.com
Website - PrairieNickelPawn.com

Somewhere on the card we would like it to say "Offering 10 Month Layaway!" & "We buy & loan on anything of value!". Our main store color is orange (please see logo). Logo does not have to be on the business card but it can be. Would like the back to have an area to write a note on the back. We like vintage things like old coins, collectables, firearms and more so think about this in the design. We want a business card as unique as our store!

Colors

Designer to choose colors to be used in the design.

Requirements
Nice to have
• Vintage Style

```html
<!DOCTYPE html>
<html lang="en">
<head>
<meta charset="utf-8">
<title>Prairie Nickel Pawn &amp; Gun – Business Card</title>
<link rel="stylesheet" href="https://fonts.googleapis.com/css2?family=Libre+Baskerville:wght@700&family=Lato:wght@400&display=swap">
<style>
  :root {
    --stage: #e6e4e1;
    --card-brown: #3a1e0c;
    --card-white: #ffffff;
    --orange: #e0652a;
    --orange-faint: #f3d9cb;
    --cream: #f6efe8;
    --rule: #5a3720;
  }
  * { box-sizing: border-box; margin: 0; padding: 0; }
  html, body { width: 1200px; height: 1200px; overflow: hidden; }
  body { background: var(--stage); position: relative; font-family: "Lato", Arial, sans-serif; }

  .card {
    position: absolute;
    left: 250px;
    width: 700px;
    height: 400px;
    box-shadow: 0 6px 18px rgba(0,0,0,.18);
  }
  .card--back {
    top: 170px;
    background: var(--card-white);
    border-radius: 70px 0 70px 0;
  }
  .card--front {
    top: 630px;
    background: var(--card-brown);
    border-radius: 0 60px 0 60px;
    color: var(--cream);
  }

  .back-mark {
    position: absolute;
    right: 70px;
    top: 95px;
    font-family: "Libre Baskerville", Georgia, serif;
    font-weight: 700;
    font-size: 26px;
    line-height: 1.25;
    text-align: center;
    color: var(--orange-faint);
    width: 240px;
  }

  .employee-name {
    position: absolute;
    left: 40px;
    top: 38px;
    font-family: "Libre Baskerville", Georgia, serif;
    font-weight: 700;
    font-size: 22px;
    letter-spacing: .5px;
    color: var(--orange);
    text-transform: uppercase;
  }

  .store-mark {
    position: absolute;
    right: 40px;
    top: 80px;
    width: 270px;
    display: flex;
    align-items: center;
    gap: 12px;
  }
  .store-mark__dot {
    flex: none;
    width: 18px;
    height: 18px;
    border-radius: 50%;
    background: var(--orange);
  }
  .store-mark__name {
    font-family: "Libre Baskerville", Georgia, serif;
    font-weight: 700;
    font-size: 28px;
    line-height: 1.2;
    color: var(--orange);
  }

  .contact-list {
    position: absolute;
    left: 40px;
    top: 200px;
    list-style: none;
    font-size: 19px;
    line-height: 27px;
  }
  .contact-list li { display: flex; align-items: center; gap: 8px; }
  .contact-list svg { width: 14px; height: 14px; fill: var(--cream); flex: none; }

  .store-address {
    position: absolute;
    right: 40px;
    top: 240px;
    text-align: right;
    font-style: normal;
    font-size: 20px;
    line-height: 25px;
  }

  .taglines {
    position: absolute;
    left: 30px;
    right: 30px;
    top: 322px;
    display: flex;
    gap: 26px;
    font-family: "Libre Baskerville", Georgia, serif;
    font-weight: 700;
    font-size: 17px;
    color: var(--orange);
  }
  .taglines__rule {
    position: absolute;
    left: 30px;
    right: 80px;
    top: 360px;
    height: 1px;
    background: var(--rule);
  }
</style>
</head>
<body>

<section class="card card--back" aria-label="Card back with note area">
  <div class="back-mark">Prairie Nickel Pawn &amp; Gun</div>
</section>

<section class="card card--front" aria-label="Card front">
  <h1 class="employee-name">Darren Kellum</h1>

  <div class="store-mark">
    <span class="store-mark__dot"></span>
    <span class="store-mark__name">Prairie Nickel Pawn &amp; Gun</span>
  </div>

  <ul class="contact-list">
    <li>
      <svg viewBox="0 0 24 24" aria-hidden="true"><path d="M6.6 10.8a15.1 15.1 0 0 0 6.6 6.6l2.2-2.2a1 1 0 0 1 1-.25 11.4 11.4 0 0 0 3.6.57 1 1 0 0 1 1 1V20a1 1 0 0 1-1 1A17 17 0 0 1 3 4a1 1 0 0 1 1-1h3.5a1 1 0 0 1 1 1c0 1.25.2 2.45.57 3.6a1 1 0 0 1-.25 1z"/></svg>
      972-613-8840
    </li>
    <li>
      <svg viewBox="0 0 24 24" aria-hidden="true"><path d="M2 5h20v14H2z M2 5l10 8 10-8" /></svg>
      PrairieNickelPawn@Mailvera.com
    </li>
    <li>
      <svg viewBox="0 0 24 24" aria-hidden="true"><path d="M12 2a10 10 0 1 0 0 20 10 10 0 0 0 0-20zm1 15h-2v-6h2zm0-8h-2V7h2z"/></svg>
      PrairieNickelPawn.com
    </li>
  </ul>

  <address class="store-address">
    2417 Hwy 53 S<br>
    Suite C Wylie<br>
    TX 75246
  </address>

  <p class="taglines">
    <span>Offering 10 Month Layaway!</span>
    <span>We buy &amp; loan on anything of value!</span>
  </p>
  <div class="taglines__rule"></div>
</section>

</body>
</html>
```